Government contracting small business needs a web design

Tarvex Summit Inc is a veteran owned small business that delivers a full range of professional services as well as training in information technology, security and defense intelligence solutions.
We need a professional/corporate looking website where potential clients can view what services are offered.
This being a new company, there is not much that can added more than a narrative statement, stock photos and a place where potential customers and employees can make contact.
Open to ideas.
Target Market(s)
US Government
Industry/Entity Type
Small Business
Look and feel
Each slider illustrates characteristics of the customer's brand and the style your logo design should communicate.

```html
<!DOCTYPE html>
<html lang="en">
<head>
<meta charset="utf-8">
<title>Tarvex Summit Inc</title>
<link rel="stylesheet" href="https://fonts.googleapis.com/css2?family=Ubuntu:wght@400;700&family=PT+Sans:ital,wght@0,400;0,700;1,400&family=Arimo:wght@400;700&display=swap">
<style>
:root{
  --ink:#222;
  --ink-soft:#444;
  --heading-grey:#4b4b4b;
  --accent-red:#7a0f00;
  --tick:#3b3418;
  --date:#5b4a00;
  --rule:#c9c4ba;
  --header-line:#9aa6a8;
  --hero-top:#d6d6d6;
  --hero-bottom:#c6c6c6;
  --body-top:#e7e1d6;
  --body-bottom:#f4f1ec;
  --footer-top:#f8d58e;
  --footer-bottom:#d99550;
}
*{margin:0;padding:0;box-sizing:border-box}
html,body{width:1200px;height:1091px;overflow:hidden}
body{position:relative;background:#fff;font-family:"PT Sans",sans-serif;color:var(--ink)}
.abs{position:absolute}

.site-header{left:0;top:0;width:1200px;height:77px;background:#fff;border-bottom:1px solid var(--header-line)}
.brand{left:92px;top:8px;display:flex;align-items:center;gap:12px}
.brand-name{font-family:"Arimo",sans-serif;font-weight:700;font-size:38px;color:#4a4a4a;letter-spacing:.5px}
.main-nav{right:100px;top:29px;display:flex;font-family:"PT Sans",sans-serif;font-style:italic;font-size:13.5px;color:#333}
.main-nav a{color:inherit;text-decoration:none}
.main-nav span{margin:0 15px}

.hero{left:0;top:77px;width:1200px;height:347px;background:linear-gradient(180deg,var(--hero-top),var(--hero-bottom));border-bottom:1px solid #b8b8b8}
.hero-visual{left:115px;top:58px;width:395px;height:272px;border-radius:6px;background:radial-gradient(circle at 78% 20%,#b89a2a 0,#8a7220 14%,transparent 15%),linear-gradient(160deg,#cfcfcf,#a8a8a8)}
.hero-title{left:601px;top:103px;font-family:"Ubuntu",sans-serif;font-size:32px;line-height:40px}
.hero-title .red{color:var(--accent-red)}
.hero-title .dark{color:var(--ink)}
.hero-list{left:590px;top:186px;list-style:none;font-family:"Arimo",sans-serif;font-size:19px;color:var(--tick);text-shadow:0 1px 0 #fff}
.hero-list li{display:flex;align-items:center;height:32px}
.hero-list svg{margin-right:6px}
.slider-dots{left:547px;top:322px;display:flex;gap:6px}
.slider-dots i{width:14px;height:14px;border-radius:50%;background:radial-gradient(circle at 40% 35%,#999,#5f5f5f)}

.content{left:0;top:424px;width:1200px;height:583px;background:linear-gradient(180deg,var(--body-top),var(--body-bottom))}
.welcome-title{left:104px;top:28px;font-family:"Arimo",sans-serif;font-weight:700;font-size:30px;color:var(--heading-grey)}
.welcome-text{left:105px;top:86px;width:732px;font-size:12.4px;line-height:18px;color:var(--ink);text-align:justify}
.welcome-text p+p{margin-top:18px}
.welcome-photo{left:881px;top:73px;width:206px;height:207px;border:1px solid #ccc;background:linear-gradient(135deg,#f7f7f7,#e2e2e2 60%,#f2a030 85%,#e67a10);box-shadow:0 1px 3px rgba(0,0,0,.25)}
.divider{left:115px;top:306px;width:965px;height:1px;background:var(--rule)}

.col-title{font-family:"Ubuntu",sans-serif;font-size:19px;color:var(--ink)}
.news{left:111px;top:326px;width:450px}
.news-item{margin-top:12px}
.news-item+.news-item{margin-top:6px}
.news-date{font-size:12.5px;color:var(--date);line-height:16px}
.news-text{font-size:13.5px;line-height:18px;color:var(--ink-soft)}
.read-more{display:inline-block;margin-top:6px;font-size:13.5px;color:var(--date);text-decoration:none;border-bottom:1px solid var(--date)}
.col-shadow{left:574px;top:320px;width:8px;height:222px;background:linear-gradient(90deg,transparent,rgba(0,0,0,.18));filter:blur(2px)}

.technology{left:607px;top:326px;width:480px}
.technology .col-title{margin-left:8px}
.tech-photo{left:607px;top:366px;width:147px;height:111px;border:1px solid #ccc;background:radial-gradient(circle at 50% 45%,#7fc0ea 0,#3a8fd0 22%,#e9f3fa 24%,#fff 70%)}
.tech-text{left:765px;top:366px;width:322px;font-size:13.2px;line-height:18px;color:var(--ink-soft);text-align:justify}
.tech-note{left:607px;top:489px;width:480px;font-size:12.4px;line-height:18px;color:var(--ink)}

.site-footer{left:0;top:1007px;width:1200px;height:84px;background:linear-gradient(180deg,var(--footer-top),var(--footer-bottom));border-top:1px solid #b9a27a}
.site-footer p{position:absolute;left:113px;top:10px;font-style:italic;font-size:13.5px;color:#222}
</style>
</head>
<body>
<header class="site-header abs">
  <div class="brand abs">
    <svg width="44" height="44" viewBox="0 0 44 44" aria-hidden="true"><circle cx="22" cy="22" r="20" fill="#5a5a5a"/></svg>
    <span class="brand-name">Tarvex Summit</span>
  </div>
  <nav class="main-nav abs">
    <a href="#">home</a><span>|</span><a href="#">about us</a><span>|</span><a href="#">services</a><span>|</span><a href="#">It Security</a><span>|</span><a href="#">Solutions</a><span>|</span><a href="#">Contact us</a>
  </nav>
</header>

<section class="hero abs">
  <div class="hero-visual abs" role="img" aria-label="Businessman with briefcase climbing stone steps toward a golden globe"></div>
  <h1 class="hero-title abs"><span class="red">IT Security and intellingence</span><br><span class="dark">security solutions</span></h1>
  <ul class="hero-list abs">
    <li><svg width="26" height="22" viewBox="0 0 26 22"><path d="M2 12 L9 19 L24 2 L10 14 Z" fill="var(--tick)"/></svg>Lorem Ipsum Dolar Sit</li>
    <li><svg width="26" height="22" viewBox="0 0 26 22"><path d="M2 12 L9 19 L24 2 L10 14 Z" fill="var(--tick)"/></svg>Amet Lorem ipsum Dolar Sipusm</li>
    <li><svg width="26" height="22" viewBox="0 0 26 22"><path d="M2 12 L9 19 L24 2 L10 14 Z" fill="var(--tick)"/></svg>Amet Lorem Ipsum Dolar Sit</li>
  </ul>
  <div class="slider-dots abs"><i></i><i></i><i></i></div>
</section>

<main class="content abs">
  <h2 class="welcome-title abs">Welcome to Tarvex Summit</h2>
  <div class="welcome-text abs">
    <p>"Lorem ipsum dolor sit amet, consectetur adipisicing elit, sed do eiusmod tempor incididunt ut labore et dolore magna aliqua. Ut enim ad minim veniam, quis nostrud exercitation ullamco laboris nisi ut aliquip ex ea commodo consequat. Duis aute irure dolor in reprehenderit in voluptate velit esse cillum dolore eu fugiat nulla pariatur. Excepteur sint occaecat cupidatat non proident, sunt in culpa qui officia deserunt mollit anim id est laborum."</p>
    <p>"Lorem ipsum dolor sit amet, consectetur adipisicing elit, sed do eiusmod tempor incididunt ut labore et dolore magna aliqua. Ut enim ad minim veniam, quis nostrud exercitation ullamco laboris nisi ut aliquip ex ea commodo consequat.<br>&nbsp;Duis aute irure dolor in reprehenderit in voluptate velit esse cillum dolore eu fugiat nulla pariatur. Excepteur sint occaecat cupidatat non proident, sunt in culpa qui officia deserunt mollit anim id est laborum."</p>
  </div>
  <div class="welcome-photo abs" role="img" aria-label="Businesswoman giving thumbs up on top of a rising bar chart"></div>
  <div class="divider abs"></div>

  <section class="news abs">
    <h3 class="col-title">In the News</h3>
    <div class="news-item">
      <p class="news-date">February 6, 2012</p>
      <p class="news-text">Lorem Ipsum is simply dummy text of the printing and typesetting industry.</p>
    </div>
    <div class="news-item">
      <p class="news-date">January 19, 2012</p>
      <p class="news-text">Lorem Ipsum is simply dummy text of the printing and typesetting industry.&nbsp; is simply dummy text of the printing and typesetting industry.</p>
    </div>
    <a class="read-more" href="#">Read More ...</a>
  </section>
  <div class="col-shadow abs"></div>

  <section class="technology abs">
    <h3 class="col-title">Technology</h3>
  </section>
  <div class="tech-photo abs" role="img" aria-label="Globe connected to networked computer users"></div>
  <p class="tech-text abs">"Lorem ipsum dolor sit amet, consectetur adipisicing elit, sed do eiusmod tempor incididunt ut labore et dolore magna aliqua. Ut enim ad minim veniam, quis nostrud exercitation ullamco laboris nisi ut aliquip ex ea commodo consequat. Duis aute irure dolor in reprehenderit in voluptate velit esse cillum dolore eu.</p>
  <p class="tech-note abs">"Lorem ipsum dolor sit amet, consectetur adipisicing elit, sed do eiusmod tempor incididunt ut labore et dolore magna aliqua.</p>
</main>

<footer class="site-footer abs">
  <p>© All Right Reserved 2011 | Privacy Policy</p>
</footer>
</body>
</html>
```